Marlow Dermal Studio - Business Banner with Brand Elements

Design:
• We would like to get a creative design for a wide banner that will go outside our medical spa clinic location. We need a designer to make a simple yet colorful and high-quality design layout. We want this banner to be eye-catching and to communicate the services we offer at our business: Laser Hair Removal | Veluxin | Lip Filler.

Requirements:
• We would like the banner to include our companies information which is the following:

Logo
“Refresh Your Skin”
Laser Hair Removal | Veluxin | Lip Filler
(520) 867-2291
www.MarlowDermalStudio.com

Colors:
• Our business colors are orange, a hint of black and white, but mostly peach/orange tones. (Orange: #f78f20 , White: #ffffff)

Fonts:
• Josefins Sans Bold & Lato

Content and images can be located here:
https://files.quibbleshare.com/share/folders/7tKwP3zRa9_LmQxVb2nD5yHc04EeJuFs8?mode=viewing

The following will give you an idea of our brand presentation:
• Our website is: www.MarlowDermalStudio.com
• Our Pictavo; @marlowdermalstudio
• Our Lumora: www.lumoranet.com/marlowdermalstudio

Target Market(s)
• Women 25 - 45

Industry/Entity Type
• Beauty

```html
<!DOCTYPE html>
<html lang="en">
<head>
<meta charset="utf-8">
<title>Marlow Dermal Studio – Refresh Your Skin</title>
<link href="https://fonts.googleapis.com/css2?family=Josefin+Sans:wght@700&family=Lato:wght@400&display=swap" rel="stylesheet">
<style>
  :root {
    --orange: #f78f20;
    --ink: #111111;
    --white: #ffffff;
    --sky: #bfe3ee;
    --sea: #5cc6d6;
    --sand: #efe2cf;
    --studio: #d9bfa4;
  }
  html, body {
    margin: 0;
    padding: 0;
    overflow: hidden;
    background: var(--white);
  }
  .banner {
    position: relative;
    width: 1200px;
    height: 457px;
    overflow: hidden;
    background: var(--white);
    font-family: "Lato", sans-serif;
    color: var(--ink);
  }
  .brand {
    position: absolute;
    left: 40px;
    top: 62px;
    display: flex;
    align-items: center;
    gap: 12px;
  }
  .brand-dot {
    width: 46px;
    height: 46px;
    border-radius: 50%;
    background: var(--orange);
  }
  .brand-name {
    font-family: "Josefin Sans", sans-serif;
    font-weight: 700;
    font-size: 28px;
    line-height: 1;
    color: var(--ink);
    padding-top: 6px;
  }
  .headline {
    position: absolute;
    left: 42px;
    top: 190px;
    margin: 0;
    font-family: "Josefin Sans", sans-serif;
    font-weight: 700;
    font-size: 48px;
    letter-spacing: 0.5px;
    line-height: 1;
    white-space: nowrap;
  }
  .services {
    position: absolute;
    left: 0;
    top: 264px;
    width: 640px;
    height: 26px;
    margin: 0;
    padding: 0;
    list-style: none;
  }
  .service {
    position: absolute;
    top: 0;
    display: flex;
    align-items: center;
    gap: 8px;
    font-family: "Josefin Sans", sans-serif;
    font-weight: 700;
    font-size: 19px;
    line-height: 26px;
    letter-spacing: 0.6px;
    text-transform: uppercase;
    color: var(--orange);
    white-space: nowrap;
  }
  .service::before {
    content: "";
    width: 20px;
    height: 20px;
    border-radius: 50%;
    background: var(--orange);
    margin-top: -4px;
    flex: none;
  }
  .service-laser { left: 43px; }
  .service-veluxin { left: 337px; }
  .service-filler { left: 470px; }
  .contact {
    position: absolute;
    left: 48px;
    top: 340px;
    margin: 0;
    font-size: 18px;
    line-height: 1.3;
    white-space: nowrap;
  }
  .contact .sep { margin: 0 12px; }
  .photo {
    position: absolute;
    border-radius: 46px;
  }
  .photo-wind {
    left: 558px; top: 0; width: 325px; height: 224px;
    background: linear-gradient(180deg, var(--sky) 0%, #d5eef3 45%, #c9a68a 75%, #7fb7c4 100%);
    border-radius: 0 0 46px 60px;
  }
  .photo-lying {
    left: 895px; top: 31px; width: 272px; height: 188px;
    background: linear-gradient(180deg, #cfe9f4 0%, var(--sea) 35%, #8fd6d6 60%, var(--sand) 100%);
  }
  .photo-hat {
    left: 655px; top: 233px; width: 225px; height: 173px;
    background: linear-gradient(180deg, #7fc4e6 0%, #9fd3ea 40%, #d8c3a5 70%, #e9e4dc 100%);
  }
  .photo-trio {
    left: 891px; top: 230px; width: 309px; height: 227px;
    background: linear-gradient(135deg, var(--studio) 0%, #c79e80 50%, #e6d2bd 100%);
    border-radius: 60px 0 0 0;
  }
  .badge {
    position: absolute;
    left: 849px;
    top: 190px;
    width: 84px;
    height: 84px;
    border-radius: 50%;
    background: var(--white);
  }
</style>
</head>
<body>
  <main class="banner">
    <div class="brand">
      <span class="brand-dot" aria-hidden="true"></span>
      <span class="brand-name">Marlow Dermal Studio</span>
    </div>

    <h1 class="headline">Refresh Your Skin</h1>

    <ul class="services">
      <li class="service service-laser">Laser Hair Removal</li>
      <li class="service service-veluxin">Veluxin</li>
      <li class="service service-filler">Lip Filler</li>
    </ul>

    <p class="contact">Phone: (520) 867-2291<span class="sep">|</span>www.MarlowDermalStudio.com</p>

    <div class="photo photo-wind" role="img" aria-label="Smiling woman with windswept hair on a sunny beach"></div>
    <div class="photo photo-lying" role="img" aria-label="Smiling woman lying on the sand by turquoise sea"></div>
    <div class="photo photo-hat" role="img" aria-label="Woman in a straw sun hat enjoying the sun at the beach"></div>
    <div class="photo photo-trio" role="img" aria-label="Three women with glowing skin posed together on a beige backdrop"></div>
    <div class="badge" aria-hidden="true"></div>
  </main>
</body>
</html>
```